Custom unique Stationary design for Logistics company

We need a custom, unique , elegant and luxurious full stationary design using our new logo, following these guidelines:
1- Business card: double sided, both sides uses the navy blue as the background main color (same as the code of the navy blue used in our logo).
2- envelope and folder: also use the same navy blue as the main background color.
3- book cover( notepad cover) : same thing with the navy blue
4- letterhead: feel free to use the combination of the colors in our logo.
5- rest of the items are up to your creativity

Target Market(s)

corporates and other businesses

Industry/Entity Type

Logistics and heavy machines contractors

Requirements
Must have
• Letterhead, business card, envelope, notepad cover, paper, file
Nice to have
• navy blue to be main background color for business card, envelope, notepad cover

```html
<!DOCTYPE html>
<html lang="en">
<head>
<meta charset="utf-8">
<title>Northvane Logistics — Presentation Folder</title>
<link rel="stylesheet" href="https://fonts.googleapis.com/css2?family=Montserrat:wght@400;500;700&family=Lato:wght@400;700&display=swap">
<style>
  :root {
    --navy: #024466;
    --orange: #e0582a;
    --paper: #ffffff;
    --paper-shade: #e6e6e6;
    --ink: #3a3a3a;
    --backdrop: #bdbcbd;
  }
  * { box-sizing: border-box; margin: 0; padding: 0; }
  html, body { width: 982px; height: 1200px; overflow: hidden; }
  body {
    background: var(--backdrop);
    font-family: "Montserrat", sans-serif;
    position: relative;
  }
  .spread {
    position: absolute;
    left: 91px;
    width: 800px;
    height: 530px;
    display: flex;
    box-shadow: 0 10px 30px rgba(0,0,0,.25);
  }
  .spread--outside { top: 40px; }
  .spread--inside { top: 630px; }
  .panel { position: relative; width: 400px; height: 530px; overflow: hidden; }

  .brand-name {
    font-family: "Montserrat", sans-serif;
    font-weight: 700;
    letter-spacing: .5px;
    display: flex;
    align-items: center;
    gap: 8px;
    white-space: nowrap;
  }
  .brand-dot { width: 12px; height: 12px; border-radius: 50%; background: var(--orange); flex: none; }

  /* Back cover */
  .back-cover { background: var(--navy); color: var(--paper); }
  .back-cover .brand-name { position: absolute; top: 86px; left: 70px; font-size: 24px; color: var(--paper); }
  .back-contact {
    position: absolute; left: 32px; bottom: 38px;
    font-size: 11px; font-weight: 500; line-height: 2; color: var(--paper);
  }
  .back-contact .row { display: flex; align-items: center; gap: 6px; white-space: nowrap; }
  .back-contact .row--address { padding-left: 60px; }
  .back-contact .icon { width: 12px; height: 12px; flex: none; }
  .icon--fill { fill: var(--paper); }
  .icon--line { fill: none; stroke: var(--paper); stroke-width: 2; }

  /* Front cover */
  .front-cover { background: linear-gradient(90deg, var(--paper-shade), var(--paper) 40%); }
  .front-cover .brand-name { position: absolute; top: 72px; left: 0; right: 0; justify-content: center; font-size: 24px; color: var(--navy); }
  .front-band { position: absolute; left: 0; bottom: 0; width: 400px; height: 16px; }

  /* Inside */
  .inside-left { background: linear-gradient(90deg, var(--paper) 0%, #e4e4e4 60%, #cfcfcf 100%); }
  .inside-right { background: linear-gradient(90deg, #cfcfcf 0%, #ececec 25%, var(--paper) 100%); }
  .pocket { position: absolute; left: 0; bottom: 0; width: 400px; height: 530px; }

  .letterhead {
    position: absolute; top: 26px; left: 28px; width: 340px; height: 480px;
    background: var(--paper);
    box-shadow: 0 2px 10px rgba(0,0,0,.2);
    padding: 20px 24px;
    color: var(--ink);
    font-family: "Lato", sans-serif;
    font-weight: 400;
  }
  .letterhead-head { position: relative; height: 58px; }
  .letterhead .brand-name { position: absolute; left: 0; bottom: 0; font-size: 13px; color: var(--navy); gap: 5px; }
  .letterhead .brand-dot { width: 7px; height: 7px; }
  .letterhead-contact {
    position: absolute; right: 0; top: 0;
    font-size: 5.5px; line-height: 1.5; color: var(--ink);
    border-left: 1px solid var(--navy); padding-left: 5px;
  }
  .letterhead-rule { height: 1px; background: var(--navy); margin: 10px 0 20px; }
  .letter { font-size: 6.2px; line-height: 1.45; font-weight: 400; }
  .letter p { margin-bottom: 7px; }
  .letter .salutation { font-weight: 700; font-size: 7.5px; color: var(--ink); }
</style>
</head>
<body>

<section class="spread spread--outside" aria-label="Folder outside">
  <div class="panel back-cover">
    <div class="brand-name"><span class="brand-dot"></span>Northvane Logistics</div>
    <div class="back-contact">
      <div class="row row--address">1420 Harbor Line Rd, Unit 18, Oakridge, ON K2P 4R7</div>
      <div class="row">
        <svg class="icon icon--fill" viewBox="0 0 24 24" aria-hidden="true"><path d="M6.6 10.8a15 15 0 0 0 6.6 6.6l2.2-2.2a1 1 0 0 1 1-.25 11.4 11.4 0 0 0 3.6.57 1 1 0 0 1 1 1V20a1 1 0 0 1-1 1A17 17 0 0 1 3 4a1 1 0 0 1 1-1h3.5a1 1 0 0 1 1 1c0 1.25.2 2.45.57 3.57a1 1 0 0 1-.25 1z"/></svg>
        010 482 7731
        <svg class="icon icon--fill" viewBox="0 0 24 24" aria-hidden="true"><path d="M2 5h20v14H2zm2 2v.5l8 5 8-5V7l-8 5z"/></svg>
        info@northvane.com
        <svg class="icon icon--line" viewBox="0 0 24 24" aria-hidden="true"><circle cx="12" cy="12" r="10"/><path d="M2 12h20M12 2c3 3 3 17 0 20M12 2c-3 3-3 17 0 20"/></svg>
        www.northvane.com
      </div>
    </div>
  </div>
  <div class="panel front-cover">
    <div class="brand-name"><span class="brand-dot"></span>Northvane Logistics</div>
    <svg class="front-band" viewBox="0 0 400 16" preserveAspectRatio="none" aria-hidden="true">
      <polygon points="0,0 220,0 206,16 0,16" fill="var(--orange)"/>
      <polygon points="228,0 400,0 400,16 214,16" fill="var(--navy)"/>
    </svg>
  </div>
</section>

<section class="spread spread--inside" aria-label="Folder inside">
  <div class="panel inside-left">
    <svg class="pocket" viewBox="0 0 400 530" aria-hidden="true">
      <path d="M0,385 L355,345 Q368,344 375,356 L400,445 L400,530 L0,530 Z" fill="var(--navy)"/>
    </svg>
  </div>
  <div class="panel inside-right">
    <article class="letterhead">
      <header class="letterhead-head">
        <div class="brand-name"><span class="brand-dot"></span>Northvane Logistics</div>
        <div class="letterhead-contact">
          1420 Harbor Line Rd, Unit 18<br>
          Oakridge, ON K2P 4R7<br>
          010 482 7731<br>
          info@northvane.com<br>
          www.northvane.com
        </div>
      </header>
      <div class="letterhead-rule"></div>
      <div class="letter">
        <p>January-03-2020</p>
        <p>Mr. Alan Reed<br>President</p>
        <p>Harlow Industries<br>48 Market Row, Suite# 6<br>City, State, 120023</p>
        <p class="salutation">Dear Mr. Alan</p>
        <p>Lorem ipsum dolor sit amet, consectetur adipisicing elit, sed do eiusmod tempor incididunt ut labore et dolore magna aliqua. Ut enim ad minim veniam, quis nostrud exercitation ullamco laboris nisi ut aliquip ex ea commodo consequat. Duis aute irure dolor in reprehenderit in voluptate velit esse cillum dolore eu fugiat nulla pariatur.</p>
        <p>Lorem ipsum dolor sit amet, consectetur adipisicing elit, sed do eiusmod tempor incididunt ut labore et dolore magna aliqua. Ut enim ad minim veniam, quis nostrud exercitation ullamco laboris nisi ut aliquip ex ea commodo consequat. Duis aute irure dolor in reprehenderit in voluptate velit esse cillum dolore eu fugiat nulla pariatur.</p>
        <p>Lorem ipsum dolor sit amet, consectetur adipisicing elit, sed do eiusmod tempor incididunt ut labore et dolore magna aliqua. Ut enim ad minim veniam, quis nostrud exercitation ullamco laboris nisi ut aliquip ex ea commodo consequat.</p>
        <p>Excepteur sint occaecat cupidatat non proident, sunt in culpa qui officia deserunt mollit anim id est laborum. re et dolore magnam aliquam quaerat voluptatem.</p>
        <p>Regards</p>
      </div>
    </article>
    <svg class="pocket" viewBox="0 0 400 530" aria-hidden="true">
      <path d="M0,530 L18,372 Q21,360 34,358 L400,318 L400,530 Z" fill="var(--navy)"/>
    </svg>
  </div>
</section>

</body>
</html>
```